Business Card Design Project

I need a business card designed from scratch. I have an existing logo that I can upload in Illustrator for modification or redesign.

The Company is called Query Lanterns http://querylanterns.com.au and we provide Search Engine Optimization services to Australian businesses. The current logo signifies an increase in visitors, profits etc...

There are no restrictions as to the redesign - colours, style etc are all open to change.

Cards will be full colour and one sided printed at http://www.cardmoxel.com.au so check their requirements for file format and sizes etc.

I will expect all original files upon completion of project.

Target Market(s)

Any business with a web site looking to improve their search engine rankings

Industry/Entity Type

Business

Requirements
Must have
• I like modern, sleek designs. Clean, not fussy, uncluttered.

```html
<!DOCTYPE html>
<html lang="en">
<head>
<meta charset="utf-8">
<title>Query Lanterns — Business Card</title>
<link href="https://fonts.googleapis.com/css2?family=Open+Sans:wght@400;700;800&display=swap" rel="stylesheet">
<style>
  :root {
    --brand-blue: #1672b8;
    --accent-yellow: #f6c512;
    --card-white: #ffffff;
    --ink: #3a3a3a;
    --backdrop: #e9e7e4;
  }
  * { box-sizing: border-box; margin: 0; padding: 0; }
  html, body { width: 1200px; height: 460px; overflow: hidden; }
  body {
    background: var(--backdrop);
    font-family: "Open Sans", Arial, sans-serif;
    position: relative;
  }
  .card {
    position: absolute;
    top: 75px;
    width: 544px;
    height: 310px;
    box-shadow: 0 2px 6px rgba(0,0,0,0.18);
  }
  .card-front { left: 44px; background: var(--card-white); overflow: hidden; }
  .card-back { left: 614px; background: var(--brand-blue); }

  .edge-bands { position: absolute; left: 0; top: 0; }

  .wordmark {
    position: absolute;
    font-weight: 800;
    letter-spacing: -0.5px;
    display: flex;
    align-items: center;
    gap: 10px;
  }
  .wordmark-dot { border-radius: 50%; flex: none; }
  .card-front .wordmark {
    left: 42px; top: 62px;
    font-size: 29px;
    color: var(--brand-blue);
  }
  .card-front .wordmark-dot { width: 16px; height: 16px; background: var(--accent-yellow); }

  .contact {
    position: absolute;
    right: 20px;
    top: 143px;
    text-align: right;
    color: var(--ink);
    font-size: 12.5px;
  }
  .contact-name { color: var(--brand-blue); font-weight: 700; font-size: 16.5px; line-height: 22px; padding-right: 0; }
  .contact-title { font-size: 12.5px; line-height: 18px; margin-bottom: 10px; }
  .contact-line { display: flex; justify-content: flex-end; align-items: center; gap: 8px; line-height: 17.5px; }
  .contact-line svg { width: 10px; height: 10px; flex: none; }
  .contact-address { margin-top: 9px; font-size: 12.5px; }

  .card-back .wordmark {
    left: 0; right: 0; top: 112px;
    justify-content: center;
    font-size: 36px;
    color: var(--card-white);
  }
  .card-back .wordmark-dot { width: 20px; height: 20px; background: var(--card-white); }
  .back-url {
    position: absolute;
    left: 0; right: 0; top: 200px;
    text-align: center;
    color: var(--card-white);
    font-size: 12.5px;
    letter-spacing: 2.2px;
  }
</style>
</head>
<body>
  <section class="card card-front">
    <svg class="edge-bands" width="20" height="310" viewBox="0 0 20 310">
      <rect x="0" y="0" width="11" height="132" fill="var(--accent-yellow)"/>
      <polygon points="0,150 14,136 14,310 0,310" fill="var(--brand-blue)"/>
    </svg>

    <div class="wordmark"><span class="wordmark-dot"></span>Query Lanterns</div>

    <div class="contact">
      <p class="contact-name">Your Name</p>
      <p class="contact-title">Title</p>
      <p class="contact-line">098 765 4321
        <svg viewBox="0 0 10 10"><circle cx="5" cy="5" r="4.5" fill="none" stroke="var(--brand-blue)" stroke-width="1"/><path d="M3.3 2.8 L4.3 2.8 L4.6 4 L4 4.5 Q4.6 5.6 5.6 6 L6.1 5.4 L7.2 5.7 L7.2 6.7 Q5 7 3.3 4.2 Z" fill="var(--brand-blue)"/></svg>
      </p>
      <p class="contact-line">098 765 4321
        <svg viewBox="0 0 10 10"><rect x="3" y="1" width="4" height="8" rx="0.8" fill="var(--brand-blue)"/><rect x="3.7" y="2" width="2.6" height="4.5" fill="#fff"/></svg>
      </p>
      <p class="contact-line">enquiry@querylanterns.com.au
        <svg viewBox="0 0 10 10"><rect x="0.5" y="2.5" width="9" height="5.5" fill="var(--brand-blue)"/><path d="M0.5 2.5 L5 5.8 L9.5 2.5" fill="none" stroke="#fff" stroke-width="0.8"/></svg>
      </p>
      <p class="contact-line">www.querylanterns.com.au
        <svg viewBox="0 0 10 10"><circle cx="5" cy="5" r="4.3" fill="var(--brand-blue)"/><path d="M1 5 H9 M5 0.8 Q2.6 5 5 9.2 M5 0.8 Q7.4 5 5 9.2" fill="none" stroke="#fff" stroke-width="0.6"/></svg>
      </p>
      <p class="contact-address">00Floor Street, City Name State Name, Contry Name</p>
    </div>
  </section>

  <section class="card card-back">
    <div class="wordmark"><span class="wordmark-dot"></span>Query Lanterns</div>
    <p class="back-url">www.querylanterns.com.au</p>
  </section>
</body>
</html>
```